Design WordPress Website for Contractor App Website

I need a graphic design for a WordPress website for our SaaS called Velumar Software. Please design the landing (Home) page first, before designing other pages. You can design other pages if your landing page is selected.

The design should be modern with a startup feel. The link to the trelvano doc below provides more information. And the attached image has the logo and some screenshots you can use. Copy text from the competitor's site listed as placeholders text or use Lorem Ipsum where needed.

https://files.trelvanodocs.net/doc/7QpXrLm2ZkW9vTbN4cHsYd1FjA8gEo3UiR6nKwBq/view?mode=share

Target Market(s)

Contractors, painters, plumbers, handymen, electricians, carpenters, landscapers, roofers, home service business.

Industry/Entity Type

Home Improvement

Number of Pages Required

5+ page

Colors
ffc214
34a6d7
9bcb3c

Requirements
Must have
• Look, professionals
Pindle Shelf and Apdex Shelf download icons
Focused on contractors
Nice to have
• Section for video

```html
<!DOCTYPE html>
<html lang="en">
<head>
<meta charset="utf-8">
<title>Velumar Software – Contractor App</title>
<link href="https://fonts.googleapis.com/css2?family=Montserrat:wght@400;500;600;700;800&family=Roboto:wght@400;500;700&display=swap" rel="stylesheet">
<style>
:root{
  --yellow:#ffbd17;
  --yellow-soft:#ffc93f;
  --blue:#2f96d3;
  --blue-deep:#2a7fc4;
  --ink:#1d1d1d;
  --text:#333;
  --muted:#9a9a9a;
  --card:#f4f4f4;
  --dark:#333333;
  --app-red:#f4411e;
  --white:#fff;
}
*{margin:0;padding:0;box-sizing:border-box}
html,body{width:1200px;height:3485px;overflow:hidden}
body{position:relative;background:var(--white);font-family:"Montserrat",sans-serif;color:var(--text)}
.abs{position:absolute}
.btn{position:absolute;display:flex;align-items:center;justify-content:center;border-radius:22px;font-weight:700;color:var(--white);font-size:16px;letter-spacing:.2px}
.btn-blue{background:var(--blue)}
.btn-yellow{background:var(--yellow)}
h2.section-title{position:absolute;font-weight:800;font-size:50px;color:var(--ink);letter-spacing:.5px;line-height:1}
p.copy{position:absolute;font-size:16.5px;line-height:27.5px;color:var(--text)}

/* header */
.logo-blob{left:0;top:0}
.logo{left:74px;top:34px;display:flex;align-items:center;gap:10px}
.logo-mark{width:48px;height:48px;border-radius:50%;background:var(--blue-deep)}
.logo-name{font-weight:800;font-size:30px;color:var(--blue-deep);letter-spacing:3px}
.nav{left:407px;top:54px;display:flex;gap:38px;font-weight:700;font-size:16px;color:var(--ink)}
.nav-login{left:1024px;top:45px;width:100px;height:38px}

/* hero */
.hero-photo{left:240px;top:0;width:360px;height:330px;background:radial-gradient(ellipse at 50% 40%,rgba(240,160,60,.55),rgba(255,189,23,0) 70%)}
.hero-title{left:168px;top:316px;font-weight:800;font-size:62px;color:var(--white);letter-spacing:1px}
.hero-copy{left:169px;top:400px;width:400px;color:#2b2b2b}
.hero-login{left:168px;top:533px;width:100px;height:39px}
.phone{position:absolute;background:#f3f3f3;border:3px solid #d6d6d6;border-radius:34px;box-shadow:0 8px 18px rgba(0,0,0,.18)}
.phone .screen{position:absolute;left:10px;right:10px;top:50px;bottom:50px;background:var(--white);overflow:hidden}
.phone .bar{height:12px;background:var(--app-red)}
.phone .navbar{position:absolute;left:0;right:0;bottom:0;height:22px;background:#111}
.row-line{position:absolute;left:12px;height:6px;border-radius:3px;background:#e3e3e3}

/* about */
.about-title{left:674px;top:838px}
.about-copy{left:674px;top:903px;width:400px}
.about-btn{left:675px;top:1034px;width:146px;height:38px}
.play{left:320px;top:940px;width:64px;height:64px;border-radius:50%;background:var(--white);display:flex;align-items:center;justify-content:center}

/* services */
.services-title{left:150px;top:1313px}
.services-copy{left:150px;top:1376px;width:420px}
.service-item{position:absolute;left:145px;display:flex;gap:22px;font-size:16.5px;line-height:27.5px;width:440px}
.service-item svg{flex:none;margin-top:2px}
.services-btn{left:150px;top:1689px;width:146px;height:38px}
.app{position:absolute;background:var(--white);box-shadow:0 6px 20px rgba(0,0,0,.22);font-family:"Roboto",sans-serif;overflow:hidden}
.app-status{height:18px;background:#e33b1a}
.app-head{height:36px;background:var(--app-red);color:var(--white);font-size:14px;font-weight:500;display:flex;align-items:center;padding-left:16px;gap:16px}
.app-foot{position:absolute;left:0;right:0;bottom:0;height:30px;background:#000}
.field{position:absolute;left:12px;width:240px;height:36px;border:1px solid #c9c9c9;border-radius:3px;font-size:11.5px;color:#333;display:flex;align-items:center;padding-left:36px}
.field small{position:absolute;left:8px;top:-7px;background:#fff;padding:0 3px;font-size:8px;color:#666}
.field i{position:absolute;left:10px;top:11px;width:12px;height:12px;border-radius:2px;background:#555}
.est-card{position:absolute;left:12px;right:12px;height:82px;border:1px solid #e2e2e2;border-radius:4px;font-size:11.5px;padding:10px 10px}
.est-card b{font-weight:700;color:#222}
.est-card .tag{position:absolute;right:10px;top:9px;border:1.5px solid var(--app-red);color:var(--app-red);border-radius:10px;font-size:9px;padding:1px 8px}
.est-card .date{position:absolute;right:10px;top:38px;font-size:10px;color:#444}
.est-card .num{position:absolute;left:10px;bottom:10px;font-weight:700;color:#222}
.est-card .amt{position:absolute;right:10px;bottom:10px;font-weight:700;color:#3a9a2a}
.est-card .inv{position:absolute;left:10px;top:38px;font-size:10px;color:#444}

/* features */
.features-title{left:708px;top:2081px}
.features-copy{left:708px;top:2140px;width:400px;color:#2b2b2b}
.store{position:absolute;top:2277px;height:42px;background:#000;border-radius:6px;color:var(--white);display:flex;align-items:center;gap:8px;padding:0 12px;border:1px solid #a6a6a6}
.store .dot{width:22px;height:22px;border-radius:4px;background:var(--white)}
.store small{display:block;font-size:8px;font-weight:500;letter-spacing:.3px}
.store span{font-size:17px;font-weight:500;line-height:1}

/* reviews */
.reviews-title{left:0;width:1200px;text-align:center;top:2721px}
.review{position:absolute;text-align:center;font-size:12.5px;line-height:23px}
.review .stars{letter-spacing:8px;font-size:17px;margin-bottom:6px}
.review .who{font-weight:700;font-size:16.5px;margin-top:26px}
.review-side{top:2845px;width:400px;height:249px;background:var(--card);border-radius:44px;color:#b6b6b6;padding-top:44px}
.review-side .stars{color:#aaa}
.review-main{left:398px;top:2821px;width:403px;height:295px;background:var(--yellow);border-radius:54px;color:#2b2b2b;padding:56px 46px 0;font-size:14px;line-height:27.5px;box-shadow:0 6px 18px rgba(0,0,0,.08)}
.review-main .stars{color:var(--white)}
.review-main .who{color:var(--white);font-size:18px;margin-top:20px}
.pager{left:545px;top:3144px;display:flex;gap:6px}
.pager i{width:24px;height:4px;background:var(--blue)}

/* footer */
.footer-nav{left:0;width:1200px;top:3328px;display:flex;justify-content:center;gap:38px;font-weight:700;font-size:16px;color:var(--white)}
.social{left:0;width:1200px;top:3376px;display:flex;justify-content:center;gap:14px}
.social i{width:12px;height:12px;border-radius:2px;background:var(--white)}
.copyright{left:0;width:1200px;top:3417px;text-align:center;font-size:15px;color:var(--white)}
</style>
</head>
<body>

<!-- HERO BACKGROUND -->
<svg class="abs" style="left:0;top:0" width="1200" height="700" viewBox="0 0 1200 700" aria-hidden="true">
  <path d="M0,0 H1200 V560 C1080,610 960,620 860,600 C760,580 700,500 620,460 C440,380 200,300 0,185 Z" fill="var(--yellow)"/>
  <path d="M0,185 C200,300 440,380 620,460 C700,500 760,580 860,600 C960,620 1080,610 1200,560 V596 C1080,660 960,676 860,660 C760,645 700,560 620,505 C440,410 200,360 0,300 Z" fill="var(--blue)"/>
  <path d="M0,0 H300 C330,0 330,110 270,125 C200,140 90,130 0,125 Z" fill="var(--white)"/>
</svg>
<div class="abs hero-photo" role="img" aria-label="Smiling woman in a warm-toned photo faded into the yellow background"></div>

<header>
  <div class="abs logo"><span class="logo-mark"></span><span class="logo-name">VELUMAR</span></div>
  <nav class="abs nav"><span>HOME</span><span>FEATURES</span><span>PRICING</span><span>SERVICES</span><span>CONTACT</span><span>BLOG</span></nav>
  <div class="btn btn-blue nav-login">LOGIN</div>
</header>

<section class="hero">
  <h1 class="abs hero-title">VELUMAR</h1>
  <p class="copy hero-copy">Lorem ipsum dolor sit amet, consectetur adipiscing elit, sed do eiusmod tempor incididunt ut labore et dolore magna aliqua. Ut enim ad minim veniam, quis nostrud</p>
  <div class="btn btn-blue hero-login">LOGIN</div>

  <div class="phone" style="left:785px;top:130px;width:230px;height:471px">
    <div class="screen"><div class="bar"></div><div class="bar" style="height:20px;background:#f4411e;opacity:.9"></div>
      <div class="row-line" style="top:60px;width:120px;left:90px"></div>
      <div class="row-line" style="top:110px;width:120px;left:90px"></div>
      <div class="row-line" style="top:180px;width:120px;left:90px"></div>
      <div class="row-line" style="top:250px;width:120px;left:90px"></div>
      <div class="abs" style="right:14px;bottom:80px;width:26px;height:26px;border-radius:50%;background:var(--app-red)"></div>
      <div class="navbar"></div></div>
  </div>
  <div class="phone" style="left:659px;top:200px;width:225px;height:460px">
    <div class="screen"><div class="bar"></div>
      <div class="abs" style="left:0;top:12px;width:160px;bottom:22px;background:#fff"></div>
      <div class="abs" style="left:160px;top:12px;right:0;bottom:22px;background:#5a5a5a"></div>
      <div class="abs" style="left:38px;top:26px;width:14px;height:14px;border-radius:50%;background:var(--blue-deep)"></div>
      <div class="abs" style="left:56px;top:28px;font:700 11px Montserrat,sans-serif;color:var(--blue-deep)">VELUMAR</div>
      <div class="abs" style="left:16px;top:48px;font:700 11px Montserrat,sans-serif;color:var(--blue-deep)">CONTRACTOR APP</div>
      <div class="abs" style="left:6px;top:112px;width:150px;height:20px;background:#fde3dc"></div>
      <div class="row-line" style="top:96px;width:90px"></div>
      <div class="row-line" style="top:120px;width:90px"></div>
      <div class="row-line" style="top:144px;width:90px"></div>
      <div class="row-line" style="top:168px;width:90px"></div>
      <div class="row-line" style="top:192px;width:90px"></div>
      <div class="row-line" style="top:216px;width:90px"></div>
      <div class="row-line" style="top:240px;width:90px"></div>
      <div class="row-line" style="top:264px;width:90px"></div>
      <div class="row-line" style="top:288px;width:90px"></div>
      <div class="navbar"></div></div>
  </div>
</section>

<!-- ABOUT -->
<section class="about">
  <svg class="abs" style="left:100px;top:705px" width="500" height="490" viewBox="0 0 500 490">
    <path d="M190,40 C280,0 380,-10 440,40 C500,90 480,230 420,330 C360,430 260,470 150,440 C40,410 -10,320 10,240 C30,160 100,80 190,40 Z" fill="#a9d8ee"/>
    <path d="M180,30 C270,-5 370,20 420,80 C470,140 460,260 390,350 C320,440 220,490 140,480 C60,470 30,390 30,300 C30,200 90,70 180,30 Z" fill="var(--yellow)"/>
    <path d="M180,24 C270,-10 370,15 418,75 C465,135 455,255 385,345 C315,435 215,480 140,470 C65,460 32,380 32,295 C32,195 92,62 180,24 Z" fill="#3c5a4a" role="img" aria-label="Woman holding a coffee cup and smiling at her phone"/>
  </svg>
  <div class="abs play"><svg width="20" height="24" viewBox="0 0 20 24"><path d="M2,0 L20,12 L2,24 Z" fill="#111"/></svg></div>
  <h2 class="section-title about-title">ABOUT US</h2>
  <p class="copy about-copy">Lorem ipsum dolor sit amet, consectetur adipiscing elit, sed do eiusmod tempor incididunt ut labore et dolore magna aliqua. Ut enim ad minim veniam, quis nostrud</p>
  <div class="btn btn-yellow about-btn">READ MORE</div>
</section>

<!-- SERVICES -->
<section class="services">
  <h2 class="section-title services-title">SERVICES</h2>
  <p class="copy services-copy">Lorem ipsum dolor sit amet, consectetur adipiscing elit, sed do eiusmod tempor .</p>
  <div class="service-item" style="top:1465px">
    <svg width="32" height="32" viewBox="0 0 32 32" fill="none" stroke="var(--yellow)" stroke-width="1.8"><path d="M8,24 C12,12 20,6 28,4 C26,12 20,20 8,24 Z"/><circle cx="20" cy="12" r="2.5"/><path d="M4,28 L10,22"/></svg>
    <span>Lorem ipsum dolor sit amet, consectetur</span></div>
  <div class="service-item" style="top:1519px">
    <svg width="32" height="32" viewBox="0 0 32 32" fill="none" stroke="var(--yellow)" stroke-width="1.8"><circle cx="16" cy="16" r="5"/><circle cx="16" cy="16" r="11" stroke-dasharray="5 3"/></svg>
    <span>Duis aute irure dolor in reprehenderit in voluptate velit</span></div>
  <div class="service-item" style="top:1601px">
    <svg width="32" height="32" viewBox="0 0 32 32" fill="none" stroke="var(--yellow)" stroke-width="1.8"><rect x="6" y="6" width="20" height="14" rx="1"/><path d="M3,24 H22"/><rect x="22" y="14" width="8" height="12" rx="1"/></svg>
    <span>Nemo enim ipsam voluptatem quia voluptas sit aspernatur aut odit aut fugit,</span></div>
  <div class="btn btn-yellow services-btn">READ MORE</div>

  <div class="app" style="left:644px;top:1306px;width:283px;height:503px">
    <div class="app-status"></div>
    <div class="app-head"><span>←</span>Company Information</div>
    <div style="background:#eee;height:30px;font-size:11px;font-weight:700;color:#2a6fb0;padding:10px 12px">ADDRESS</div>
    <div class="field" style="top:134px"><small>Address Line 1</small><i></i>418 Harrow Lane</div>
    <div class="field" style="top:180px"><small>City</small><i></i>Fenwick</div>
    <div class="field" style="top:226px"><small>State or Province</small><i></i>Oregon</div>
    <div class="field" style="top:272px"><small>Zip or Postal Code</small><i></i>97204</div>
    <div class="field" style="top:318px"><small>Country</small><i></i>United States</div>
    <div class="abs" style="left:0;right:0;top:390px;height:30px;background:#eee;font-size:10px;font-weight:700;color:#2a6fb0;padding:9px 12px">WEBSITE AND SOCIAL MEDIA</div>
    <div class="abs" style="left:12px;right:12px;top:424px;height:30px;background:var(--app-red);border-radius:2px"></div>
    <div class="app-foot"></div>
  </div>

  <div class="app" style="left:820px;top:1403px;width:271px;height:479px">
    <div class="app-status"></div>
    <div class="app-head">≡ <span>Estimates</span></div>
    <div style="height:30px;display:flex;justify-content:space-around;align-items:center;font-size:9.5px;font-weight:700;color:#333;border-bottom:1px solid #eee"><span style="color:var(--app-red)">ALL</span><span>CLOSED</span><span>OPEN</span><span>DRAFT</span></div>
    <div class="est-card" style="top:92px"><b>Dara Quenwick</b><span class="tag">Closed</span><span class="inv">INV-90245</span><span class="date">Aug 30, 2020</span><span class="num">EST-1029</span><span class="amt">$300.91</span></div>
    <div class="est-card" style="top:185px"><b>Tobin Marchetti</b><span class="tag">Rejected</span><span class="date">Aug 30, 2020</span><span class="num">EST-2098</span><span class="amt">$1,306.94</span></div>
    <div class="est-card" style="top:278px"><b>Lena Brostow</b><span class="tag">Draft</span><span class="date">Aug 30, 2020</span><span class="num">EST-24945</span><span class="amt">$946.92</span></div>
    <div class="est-card" style="top:371px;height:40px"><b>Orin Vasquell</b></div>
    <div class="abs" style="right:10px;top:362px;width:32px;height:32px;border-radius:50%;background:var(--app-red)"></div>
    <div class="abs" style="left:16px;top:414px;width:90px;height:26px;border-radius:13px;background:#2a6fd8;color:#fff;font-size:10px;display:flex;align-items:center;justify-content:center">Sort By Date</div>
    <div class="abs" style="left:114px;top:414px;width:96px;height:26px;border-radius:13px;border:1px solid #ccc;font-size:10px;display:flex;align-items:center;justify-content:center">Sort By Client</div>
    <div class="app-foot"></div>
  </div>
</section>

<!-- FEATURES -->
<svg class="abs" style="left:0;top:2000px" width="1200" height="720" viewBox="0 0 1200 720" aria-hidden="true">
  <path d="M0,0 H1200 V700 C1050,700 920,660 800,560 C700,480 560,420 400,380 C250,340 120,340 0,380 Z" fill="var(--yellow)"/>
  <path d="M0,330 C120,290 260,300 400,340 C560,385 700,440 800,530 C920,640 1050,690 1200,690 V705 C1050,705 910,660 790,560 C690,480 560,420 400,385 C250,350 120,360 0,395 Z" fill="var(--blue)"/>
</svg>
<section class="features">
  <div class="abs" style="left:142px;top:2200px;width:264px;height:195px;background:linear-gradient(135deg,#f2f2f2,#dcdcdc)" role="img" aria-label="Isometric app screens mockup in grey and red"></div>
  <div class="abs" style="left:268px;top:2061px;width:333px;height:222px;background:linear-gradient(160deg,#8a7a6a,#4a5a70)" role="img" aria-label="Couple sitting on steps looking at their phones"></div>
  <div class="abs" style="left:364px;top:2276px;width:304px;height:176px;background:linear-gradient(135deg,#f6f6f6,#e0e0e0)" role="img" aria-label="Isometric phone showing the app over a screen flow diagram"></div>
  <h2 class="section-title features-title">FEATURES</h2>
  <p class="copy features-copy">Lorem ipsum dolor sit amet, consectetur adipiscing elit, sed do eiusmod tempor incididunt ut labore et dolore magna aliqua. Ut enim ad minim veniam, quis nostrud</p>
  <div class="store" style="left:709px;width:146px"><span class="dot"></span><div><small>GET IT ON</small><span>Pindle Shelf</span></div></div>
  <div class="store" style="left:863px;width:142px"><span class="dot"></span><div><small>Download on the</small><span>Apdex Shelf</span></div></div>
</section>

<!-- REVIEWS -->
<section class="reviews">
  <h2 class="section-title reviews-title">REVIEWS</h2>
  <div class="review review-side" style="left:141px;padding-right:80px;padding-left:40px">
    <div class="stars">★★★★★</div>
    <p>Lorem ipsum dolor sit amet, consectetur adipiscing elit, sed do eiusmod tempor incididunt ut labore et dolore magna aliqua. Ut enim ad minim veniam, quis nostrud</p>
    <p class="who">- Lorium dolor</p></div>
  <div class="review review-side" style="left:674px;padding-left:80px;padding-right:40px">
    <div class="stars">★★★★★</div>
    <p>Lorem ipsum dolor sit amet, consectetur adipiscing elit, sed do eiusmod tempor incididunt ut labore et dolore magna aliqua. Ut enim ad minim veniam, quis nostrud</p>
    <p class="who">- Lorium dolor</p></div>
  <div class="review review-main">
    <div class="stars">★★★★★</div>
    <p>Lorem ipsum dolor sit amet, consectetur adipiscing elit, sed do eiusmod tempor incididunt ut labore et dolore magna aliqua. Ut enim ad minim veniam, quis nostrud</p>
    <p class="who">- Lorium dolor</p></div>
  <div class="abs pager"><i></i><i></i><i></i><i></i></div>
</section>

<!-- FOOTER -->
<svg class="abs" style="left:0;top:3110px" width="1200" height="375" viewBox="0 0 1200 375" aria-hidden="true">
  <path d="M0,60 C250,20 450,110 700,90 C900,75 1050,40 1200,40 V375 H0 Z" fill="#ececec"/>
  <path d="M0,110 C60,30 200,10 330,60 C470,110 600,190 780,170 C950,150 1080,70 1200,80 V375 H0 Z" fill="var(--dark)"/>
</svg>
<footer>
  <nav class="abs footer-nav"><span>HOME</span><span>FEATURES</span><span>PRICING</span><span>SERVICES</span><span>CONTACT</span><span>BLOG</span></nav>
  <div class="abs social"><i></i><i></i></div>
  <p class="abs copyright">© 2021 &nbsp;|&nbsp; www.velumarsoftware.com</p>
</footer>

</body>
</html>
```